Corvane Holdings , new business card design

investment firm with corporate clients . need double sided business card , vertical and horizontal options ,logo must be clear. prefer pantone colors only and sharp design. website also www.corvane.ae

Khalid Bin Tarrafi
Managing Director
Tel. +971 4 387 2940
Mobile +971 50 518 2403
khalid@corvane.ae
Q-Span Plaza, officw 18-B07, Warqa Gardens, Dubai

Contact Information for Business Card

Khalid Bin Tarrafi
Managing Director

Font styles to use
Serif

Colors

Designer to choose colors to be used in the design.

```html
<!DOCTYPE html>
<html lang="en">
<head>
<meta charset="utf-8">
<title>Corvane Holdings – Business Card</title>
<link rel="stylesheet" href="https://fonts.googleapis.com/css2?family=Roboto+Condensed:wght@700&family=Roboto:wght@300;400;500&display=swap">
<style>
  :root {
    --stage: #e8e5e1;
    --card-front: #f4f4f4;
    --card-back: #487497;
    --brand-blue: #4a729a;
    --ink-dark: #1c1c1c;
    --ink-body: #4d4d4d;
    --on-blue: #ffffff;
  }
  html, body {
    margin: 0;
    padding: 0;
    width: 1200px;
    height: 960px;
    overflow: hidden;
    background: var(--stage);
  }
  .canvas {
    position: relative;
    width: 1200px;
    height: 960px;
  }
  .card {
    position: absolute;
    width: 598px;
    height: 342px;
    box-sizing: border-box;
  }
  .card--front {
    left: 322px;
    top: 108px;
    background: var(--card-front);
  }
  .card--back {
    left: 320px;
    top: 494px;
    height: 340px;
    background: var(--card-back);
    display: flex;
    align-items: center;
    justify-content: center;
  }
  .holder {
    position: absolute;
    right: 28px;
    top: 26px;
    text-align: right;
  }
  .holder__name {
    margin: 0;
    font-family: "Roboto Condensed", "Arial Narrow", sans-serif;
    font-weight: 700;
    font-size: 21px;
    line-height: 26px;
    color: var(--brand-blue);
    text-transform: uppercase;
  }
  .holder__title {
    margin: 0;
    font-family: "Roboto", Arial, sans-serif;
    font-weight: 500;
    font-size: 14.5px;
    line-height: 18px;
    letter-spacing: 0.3px;
    color: var(--ink-dark);
    text-transform: uppercase;
  }
  .contact {
    position: absolute;
    left: 29px;
    top: 237px;
    font-family: "Roboto", Arial, sans-serif;
    font-weight: 400;
    font-size: 14px;
    line-height: 18.5px;
    color: var(--ink-body);
  }
  .contact p { margin: 0; }
  .contact__address { margin-bottom: 5px !important; }
  .contact__lines { padding-left: 1px; }
  .brand-name {
    margin: 0;
    font-family: "Roboto", Arial, sans-serif;
    font-weight: 300;
    font-size: 40px;
    letter-spacing: 10px;
    color: var(--on-blue);
    text-transform: uppercase;
    text-align: center;
    line-height: 1;
    padding-left: 10px;
  }
</style>
</head>
<body>
<main class="canvas">
  <section class="card card--front" aria-label="Business card front">
    <header class="holder">
      <h1 class="holder__name">Khalid Bin Tarrafi</h1>
      <p class="holder__title">Managing Director</p>
    </header>
    <address class="contact">
      <p>Q-Span Plaza, officw 18-B07</p>
      <p class="contact__address">Warqa Gardens, Dubai</p>
      <div class="contact__lines">
        <p>P. +971 4 387 2940&nbsp; M.+971 50 518 2403</p>
        <p>E. khalid@corvane.ae W. www.corvane.ae</p>
      </div>
    </address>
  </section>

  <section class="card card--back" aria-label="Business card back">
    <p class="brand-name">Corvane Holdings</p>
  </section>
</main>
</body>
</html>
```